Create a business promotion flyer to leave in customer mailboxes. We are a bulk petroleum supplier, servicing any industry that requires diesel. Base in griffith NSW, servicing griffith area and surrounds.

Business Name - Terra Diesel
Fuel@terradiesel-example.com.au
Owen - 0491 570 362 ohartley@terradiesel-example.com.au
Liam - 0491 570 718 lprosser@terradiesel-example.com.au
Simon - 0491 570 905 skenway@terradiesel-example.com.au
Office 02 5550 1734

Bulk Fuel deliveries.
Oils & lubricants
Local Family owned business

```html
<!DOCTYPE html>
<html lang="en">
<head>
<meta charset="utf-8">
<title>Terra Diesel – Bulk Fuel Delivery Flyer</title>
<link href="https://fonts.googleapis.com/css2?family=Archivo:wght@500;700;800;900&family=Inter:wght@500;600&family=Roboto+Condensed:wght@500;700&family=Caveat:wght@500&display=swap" rel="stylesheet">
<style>
:root{
  --red:#e11d24;
  --ink:#333436;
  --text:#2b2b2b;
  --grey:#595a5c;
  --rule:#d9d9d9;
  --footer:#3a3a3b;
  --white:#ffffff;
  --concrete:#d6d2cc;
}
*{margin:0;padding:0;box-sizing:border-box}
html,body{width:849px;height:1200px;overflow:hidden;background:#fff}
.flyer{position:relative;width:849px;height:1200px;overflow:hidden;background:#fff;font-family:"Inter",Arial,sans-serif;color:var(--text)}
.abs{position:absolute}

/* hero */
.hero-photo{left:260px;top:0;width:589px;height:545px;
  background:linear-gradient(180deg,#3f83d2 0%,#8fb6e4 22%,#c9cdd2 45%,#e2ddd6 70%,var(--concrete) 100%)}
.hero-fade{left:0;top:0;width:849px;height:545px;
  background:linear-gradient(90deg,#fff 0%,#fff 34%,rgba(255,255,255,.85) 44%,rgba(255,255,255,0) 62%),
             linear-gradient(0deg,#fff 0%,rgba(255,255,255,0) 14%)}
.brand{left:34px;top:46px;display:flex;align-items:center;gap:10px}
.brand-dot{width:22px;height:22px;border-radius:50%;background:var(--red)}
.brand-name{font-family:"Archivo",Arial,sans-serif;font-weight:700;font-size:40px;color:var(--red);letter-spacing:-.5px}
.headline{left:34px;top:178px;font-family:"Archivo",Arial,sans-serif;font-weight:900;font-size:60px;line-height:54px;letter-spacing:-.5px;color:var(--ink)}
.headline .accent{color:var(--red)}
.subhead{left:34px;top:342px;font-family:"Archivo",Arial,sans-serif;font-weight:500;font-size:24px;line-height:28px;color:var(--ink)}
.accent-line{left:34px;top:411px;width:64px;height:3px;background:var(--red)}
.intro{left:34px;top:432px;width:315px;font-size:13.3px;line-height:19px;font-weight:600;color:var(--text)}

/* features */
.features{left:34px;top:544px;width:781px;height:93px;border-top:1px solid var(--rule);border-bottom:1px solid var(--rule);display:flex;align-items:center;justify-content:space-between}
.feature{display:flex;align-items:center;gap:12px;height:52px;flex:none}
.feature+.feature{border-left:1px solid var(--rule);padding-left:16px}
.feature svg{flex:none}
.feature-label{font-family:"Roboto Condensed",Arial,sans-serif;font-weight:500;font-size:13.5px;line-height:17px;color:var(--ink);white-space:nowrap;padding-right:10px}
.feature:last-child .feature-label{padding-right:0}

/* services */
.services-title{left:34px;top:648px;width:781px;display:flex;align-items:center;gap:18px}
.services-title span{font-family:"Archivo",Arial,sans-serif;font-weight:800;font-size:19px;color:var(--ink);white-space:nowrap}
.services-title i{flex:1;height:1px;background:#ef6b6f}
.service{top:714px;width:244px}
.service-photo{width:244px;height:139px}
.service-icon{position:absolute;top:-25px;left:50%;margin-left:-26px;width:52px;height:52px;border-radius:50%;background:var(--red);border:3px solid #fff;display:flex;align-items:center;justify-content:center}
.service-title{margin:12px 0 0 5px;font-family:"Archivo",Arial,sans-serif;font-weight:800;font-size:16px;color:var(--red)}
.service-text{margin:5px 0 0 5px;font-size:12.6px;line-height:18px;font-weight:500;color:var(--text);width:210px}
.service-divider{top:703px;width:1px;height:237px;background:var(--rule)}
.photo-fuel{background:linear-gradient(180deg,#7c7a80 0%,#d39a5a 45%,#8a6a45 75%,#4a3a28 100%)}
.photo-oil{background:linear-gradient(180deg,#5c5650 0%,#8a857e 40%,#47618a 70%,#9a958d 100%)}
.photo-team{background:linear-gradient(180deg,#a9b8c8 0%,#e6e8ea 45%,#c4c0b8 100%)}

/* footer */
.footer{left:0;top:967px;width:849px;height:199px;background:var(--footer);color:#fff}
.cta{left:34px;top:26px;font-family:"Roboto Condensed",Arial,sans-serif;font-weight:700;font-size:18.5px;line-height:25px}
.cta .accent{color:var(--red)}
.cta-phone{left:31px;top:90px;width:46px;height:46px;border-radius:50%;background:#fff;display:flex;align-items:center;justify-content:center}
.tagline{left:88px;top:92px;font-family:"Caveat",cursive;font-size:21px;line-height:22px;color:#fff;transform:rotate(-4deg);transform-origin:left top}
.tagline-line{left:90px;top:142px;width:110px;height:2px;background:var(--red);transform:rotate(-5deg)}
.vrule{width:0;border-left:1px dashed #8a8a8a}
.contact{top:26px;width:186px;font-family:"Roboto Condensed",Arial,sans-serif}
.contact-name{font-weight:700;font-size:16px;color:var(--red);text-transform:uppercase;margin-bottom:10px}
.contact-row{display:flex;align-items:center;gap:7px;font-size:13px;height:20px;margin-bottom:8px;white-space:nowrap}
.contact-row.small{font-size:9.8px;letter-spacing:-.1px}
.ic{width:17px;height:17px;border-radius:50%;background:#fff;display:flex;align-items:center;justify-content:center;flex:none}
.hrule{left:226px;top:120px;width:590px;height:1px;background:#6a6a6a}
.office{top:139px;display:flex;align-items:center;gap:10px;font-family:"Roboto Condensed",Arial,sans-serif;font-size:14px;white-space:nowrap}
.office .ic{width:20px;height:20px}
.band{left:0;top:1166px;width:849px;height:34px;background:var(--red);color:#fff;display:flex;align-items:center;justify-content:center;gap:14px;font-family:"Archivo",Arial,sans-serif;font-weight:700;font-size:14.5px;letter-spacing:1.2px}
</style>
</head>
<body>
<div class="flyer">

  <div class="abs hero-photo" role="img" aria-label="Photo of a white branded fuel tanker truck parked outside a steel depot shed under a blue sky"></div>
  <div class="abs hero-fade"></div>

  <div class="abs brand">
    <span class="brand-dot"></span>
    <span class="brand-name">Terra Diesel</span>
  </div>

  <h1 class="abs headline">RELIABLE<br><span class="accent">BULK FUEL</span><br>DELIVERY</h1>
  <p class="abs subhead">ACROSS GRIFFITH &amp;<br>SURROUNDING AREAS</p>
  <div class="abs accent-line"></div>
  <p class="abs intro">Local family-owned fuel supplier providing dependable diesel deliveries, premium lubricants and outstanding service to farms, transport, construction, industrial and commercial businesses.</p>

  <div class="abs features">
    <div class="feature">
      <svg width="52" height="48" viewBox="0 0 52 48"><path d="M3 20 L26 4 L49 20" fill="none" stroke="var(--red)" stroke-width="3"/><circle cx="15" cy="28" r="5" fill="var(--red)"/><circle cx="26" cy="25" r="6" fill="var(--red)"/><circle cx="37" cy="28" r="5" fill="var(--red)"/><path d="M6 46 q0-11 9-11 q9 0 9 11z M17 46 q0-13 9-13 q9 0 9 13z M28 46 q0-11 9-11 q9 0 9 11z" fill="var(--red)"/></svg>
      <span class="feature-label">LOCAL FAMILY<br>BUSINESS</span>
    </div>
    <div class="feature">
      <svg width="48" height="44" viewBox="0 0 48 44"><path d="M8 38 A20 20 0 1 1 40 38" fill="none" stroke="var(--red)" stroke-width="3"/><path d="M24 28 L33 17" stroke="var(--red)" stroke-width="3" stroke-linecap="round"/><circle cx="24" cy="28" r="3" fill="var(--red)"/><path d="M24 6v4 M10 14l3 3 M38 14l-3 3" stroke="var(--red)" stroke-width="2"/></svg>
      <span class="feature-label">FAST &amp; RELIABLE<br>DELIVERY</span>
    </div>
    <div class="feature">
      <svg width="46" height="46" viewBox="0 0 46 46"><circle cx="23" cy="23" r="20" fill="none" stroke="var(--red)" stroke-width="3"/><text x="23" y="31" text-anchor="middle" font-family="Archivo,Arial,sans-serif" font-weight="700" font-size="24" fill="var(--red)">$</text></svg>
      <span class="feature-label">COMPETITIVE<br>PRICING</span>
    </div>
    <div class="feature">
      <svg width="38" height="46" viewBox="0 0 38 46"><rect x="2" y="3" width="24" height="40" rx="3" fill="var(--red)"/><rect x="6" y="8" width="16" height="10" fill="#fff"/><path d="M14 25 q-4 6 0 8 q4-2 0-8z" fill="#fff"/><path d="M26 12 l6 5 v18 q0 4 -3 4 q-3 0 -3-4 v-8" fill="none" stroke="var(--red)" stroke-width="2.5"/></svg>
      <span class="feature-label">RELIABLE<br>SUPPLY</span>
    </div>
    <div class="feature">
      <svg width="36" height="48" viewBox="0 0 36 48"><path d="M18 3 C10 16 3 24 3 31 a15 15 0 0 0 30 0 C33 24 26 16 18 3z" fill="none" stroke="var(--red)" stroke-width="3"/><path d="M11 30 q0 8 8 9" fill="none" stroke="var(--red)" stroke-width="2.5"/></svg>
      <span class="feature-label">PREMIUM<br>LUBRICANTS</span>
    </div>
  </div>

  <div class="abs services-title"><i></i><span>OUR SERVICES</span><i></i></div>

  <div class="abs service" style="left:35px">
    <div class="service-photo photo-fuel" role="img" aria-label="Photo of a tractor beside a large steel fuel silo at sunset"></div>
    <div class="service-icon"><svg width="24" height="26" viewBox="0 0 24 26"><rect x="2" y="2" width="13" height="22" rx="2" fill="#fff"/><rect x="5" y="5" width="7" height="5" fill="var(--red)"/><path d="M15 7 l5 4 v9 q0 2 -2 2 q-2 0 -2-2 v-4" fill="none" stroke="#fff" stroke-width="2"/></svg></div>
    <h2 class="service-title">BULK DIESEL DELIVERY</h2>
    <p class="service-text">Reliable scheduled and emergency fuel deliveries to keep your business moving.</p>
  </div>
  <div class="abs service-divider" style="left:290px"></div>

  <div class="abs service" style="left:302px">
    <div class="service-photo photo-oil" role="img" aria-label="Photo of assorted lubricant oil containers lined up in a workshop"></div>
    <div class="service-icon"><svg width="22" height="28" viewBox="0 0 22 28"><path d="M11 2 C6 10 2 14 2 19 a9 9 0 0 0 18 0 C20 14 16 10 11 2z" fill="#fff"/><path d="M7 18 q0 5 5 6" fill="none" stroke="var(--red)" stroke-width="2"/></svg></div>
    <h2 class="service-title">OILS &amp; LUBRICANTS</h2>
    <p class="service-text">Premium oils and lubricants for agricultural, transport and industrial equipment.</p>
  </div>
  <div class="abs service-divider" style="left:556px"></div>

  <div class="abs service" style="left:568px">
    <div class="service-photo photo-team" role="img" aria-label="Photo of three staff in hi-vis workwear standing in front of a fuel tanker truck"></div>
    <div class="service-icon"><svg width="30" height="22" viewBox="0 0 30 22"><circle cx="8" cy="7" r="4" fill="#fff"/><circle cx="15" cy="5" r="4.5" fill="#fff"/><circle cx="22" cy="7" r="4" fill="#fff"/><path d="M1 21 q0-8 7-8 q7 0 7 8z M8 21 q0-10 7-10 q7 0 7 10z M15 21 q0-8 7-8 q7 0 7 8z" fill="#fff"/></svg></div>
    <h2 class="service-title">LOCAL SUPPORT</h2>
    <p class="service-text">Fast, friendly support from a trusted Griffith-based family business.</p>
  </div>

  <footer class="abs footer">
    <p class="abs cta">CALL YOUR LOCAL<br><span class="accent">FUEL TEAM TODAY</span></p>
    <div class="abs cta-phone"><svg width="22" height="22" viewBox="0 0 24 24"><path d="M6.6 10.8a15 15 0 0 0 6.6 6.6l2.2-2.2a1 1 0 0 1 1-.25 11.4 11.4 0 0 0 3.6.6 1 1 0 0 1 1 1V20a1 1 0 0 1-1 1A17 17 0 0 1 3 4a1 1 0 0 1 1-1h3.5a1 1 0 0 1 1 1c0 1.25.2 2.45.6 3.6a1 1 0 0 1-.25 1z" fill="var(--footer)"/></svg></div>
    <p class="abs tagline">We're here when<br>&nbsp;you need us.</p>
    <div class="abs tagline-line"></div>

    <div class="abs vrule" style="left:226px;top:18px;height:160px"></div>
    <div class="abs vrule" style="left:427px;top:18px;height:90px"></div>
    <div class="abs vrule" style="left:628px;top:18px;height:90px"></div>

    <div class="abs contact" style="left:238px">
      <p class="contact-name">Owen</p>
      <p class="contact-row"><span class="ic"><svg width="10" height="10" viewBox="0 0 24 24"><path d="M6.6 10.8a15 15 0 0 0 6.6 6.6l2.2-2.2a1 1 0 0 1 1-.25 11.4 11.4 0 0 0 3.6.6 1 1 0 0 1 1 1V20a1 1 0 0 1-1 1A17 17 0 0 1 3 4a1 1 0 0 1 1-1h3.5a1 1 0 0 1 1 1c0 1.25.2 2.45.6 3.6a1 1 0 0 1-.25 1z" fill="var(--footer)"/></svg></span>0491 570 362</p>
      <p class="contact-row small"><span class="ic"><svg width="10" height="8" viewBox="0 0 20 14"><rect x="1" y="1" width="18" height="12" rx="1" fill="none" stroke="var(--footer)" stroke-width="2"/><path d="M1 1l9 7 9-7" fill="none" stroke="var(--footer)" stroke-width="2"/></svg></span>ohartley@terradiesel-example.com.au</p>
    </div>
    <div class="abs contact" style="left:439px">
      <p class="contact-name">Liam</p>
      <p class="contact-row"><span class="ic"><svg width="10" height="10" viewBox="0 0 24 24"><path d="M6.6 10.8a15 15 0 0 0 6.6 6.6l2.2-2.2a1 1 0 0 1 1-.25 11.4 11.4 0 0 0 3.6.6 1 1 0 0 1 1 1V20a1 1 0 0 1-1 1A17 17 0 0 1 3 4a1 1 0 0 1 1-1h3.5a1 1 0 0 1 1 1c0 1.25.2 2.45.6 3.6a1 1 0 0 1-.25 1z" fill="var(--footer)"/></svg></span>0491 570 718</p>
      <p class="contact-row small"><span class="ic"><svg width="10" height="8" viewBox="0 0 20 14"><rect x="1" y="1" width="18" height="12" rx="1" fill="none" stroke="var(--footer)" stroke-width="2"/><path d="M1 1l9 7 9-7" fill="none" stroke="var(--footer)" stroke-width="2"/></svg></span>lprosser@terradiesel-example.com.au</p>
    </div>
    <div class="abs contact" style="left:640px">
      <p class="contact-name">Simon</p>
      <p class="contact-row"><span class="ic"><svg width="10" height="10" viewBox="0 0 24 24"><path d="M6.6 10.8a15 15 0 0 0 6.6 6.6l2.2-2.2a1 1 0 0 1 1-.25 11.4 11.4 0 0 0 3.6.6 1 1 0 0 1 1 1V20a1 1 0 0 1-1 1A17 17 0 0 1 3 4a1 1 0 0 1 1-1h3.5a1 1 0 0 1 1 1c0 1.25.2 2.45.6 3.6a1 1 0 0 1-.25 1z" fill="var(--footer)"/></svg></span>0491 570 905</p>
      <p class="contact-row small"><span class="ic"><svg width="10" height="8" viewBox="0 0 20 14"><rect x="1" y="1" width="18" height="12" rx="1" fill="none" stroke="var(--footer)" stroke-width="2"/><path d="M1 1l9 7 9-7" fill="none" stroke="var(--footer)" stroke-width="2"/></svg></span>skenway@terradiesel-example.com.au</p>
    </div>

    <div class="abs hrule"></div>
    <p class="abs office" style="left:243px"><span class="ic"><svg width="12" height="12" viewBox="0 0 24 24"><path d="M6.6 10.8a15 15 0 0 0 6.6 6.6l2.2-2.2a1 1 0 0 1 1-.25 11.4 11.4 0 0 0 3.6.6 1 1 0 0 1 1 1V20a1 1 0 0 1-1 1A17 17 0 0 1 3 4a1 1 0 0 1 1-1h3.5a1 1 0 0 1 1 1c0 1.25.2 2.45.6 3.6a1 1 0 0 1-.25 1z" fill="var(--footer)"/></svg></span>OFFICE 02 5550 1734</p>
    <div class="abs" style="left:423px;top:136px;width:1px;height:26px;background:#8a8a8a"></div>
    <p class="abs office" style="left:442px"><span class="ic"><svg width="11" height="9" viewBox="0 0 20 14"><rect x="1" y="1" width="18" height="12" rx="1" fill="none" stroke="var(--footer)" stroke-width="2"/><path d="M1 1l9 7 9-7" fill="none" stroke="var(--footer)" stroke-width="2"/></svg></span>Fuel@terradiesel-example.com.au</p>
  </footer>

  <div class="abs band">
    <svg width="14" height="19" viewBox="0 0 14 19"><path d="M7 0a7 7 0 0 0-7 7c0 5 7 12 7 12s7-7 7-12a7 7 0 0 0-7-7z" fill="#fff"/><circle cx="7" cy="7" r="2.6" fill="var(--red)"/></svg>
    <span>BASED IN GRIFFITH NSW</span><span>|</span><span>SERVICING GRIFFITH &amp; SURROUNDS</span>
  </div>

</div>
</body>
</html>
```